Norvane Stationery Design Project

We need stationary design that goes with the attached logo. We have logo in two different versions. One in Red/Black and the other in Blue/Green. Red/Black is going to be our primary color and we are planning to use Blue/Green occasionally as necessary.

So we need stationary design in both color combinations. Maybe you can work with Red/Black first and once we decide on the design, then you can show the Blue/Green variation.

Please see the attached png and psd files for logo.

Target Market(s)

IT departments of Medium size Enterprises.

Industry/Entity Type

Work

Requirements
Must have
• -Letter head
-Cover page design for white papers and articles that are going to publish
-Business Card
-Envelope design
Nice to have
• - High level design template that we can follow for our internal web applications

```html
<!DOCTYPE html>
<html lang="en">
<head>
<meta charset="utf-8">
<title>Norvane Software – Business Card</title>
<link href="https://fonts.googleapis.com/css2?family=Lato:wght@300;400;700;900&display=swap" rel="stylesheet">
<style>
  :root {
    --stage: #2b2b2b;
    --red-light: #e3151a;
    --red-dark: #a80c10;
    --white: #ffffff;
    --paper: #f4f4f4;
    --ink: #1a1a1a;
    --soft-pink: #f3c9ca;
    --contact: #f1e3e3;
  }
  * { margin: 0; padding: 0; box-sizing: border-box; }
  html, body { width: 1200px; height: 997px; overflow: hidden; }
  body {
    background: var(--stage);
    font-family: "Lato", sans-serif;
    position: relative;
  }
  .card {
    position: absolute;
    top: 350px;
    width: 520px;
    height: 297px;
    border-radius: 20px;
    overflow: hidden;
    box-shadow: 0 14px 30px rgba(0,0,0,0.55);
  }
  /* Front side */
  .card-front {
    left: 50px;
    background: linear-gradient(160deg, var(--red-light), var(--red-dark));
    color: var(--white);
  }
  .card-front .brand {
    position: absolute;
    left: 0; right: 0; top: 92px;
    display: flex; align-items: center; justify-content: center; gap: 14px;
  }
  .brand-mark { width: 22px; height: 22px; background: currentColor; }
  .brand-name {
    font-weight: 900;
    font-size: 34px;
    letter-spacing: 4px;
    text-transform: uppercase;
    line-height: 1;
  }
  .card-front .slogan {
    position: absolute;
    left: 0; right: 0; top: 196px;
    text-align: center;
    font-size: 13px;
    letter-spacing: 5px;
    color: var(--soft-pink);
    text-transform: uppercase;
  }
  /* Back side */
  .card-back {
    left: 630px;
    background: linear-gradient(180deg, var(--white), var(--paper));
  }
  .card-back .brand {
    position: absolute;
    left: 110px; top: 52px;
    display: flex; align-items: center; gap: 12px;
    color: var(--red-light);
  }
  .card-back .brand-name { font-size: 28px; letter-spacing: 3px; }
  .card-back .band {
    position: absolute;
    left: 0; right: 0; top: 160px; bottom: 0;
    background: linear-gradient(180deg, var(--red-light), var(--red-dark));
  }
  .card-back .rules {
    position: absolute;
    left: 0; right: 0; top: 136px;
  }
  .rule { height: 3px; background: var(--red-light); margin-bottom: 5px; }
  .holder {
    position: absolute;
    left: 28px; top: 222px;
    color: var(--white);
  }
  .holder-name { font-size: 24px; font-weight: 300; letter-spacing: 1px; text-transform: uppercase; }
  .holder-title { font-size: 14px; font-weight: 700; margin-top: 2px; color: var(--contact); }
  .contacts {
    position: absolute;
    right: 26px; top: 176px;
    list-style: none;
    color: var(--contact);
    font-size: 13px;
  }
  .contacts li { display: flex; align-items: center; gap: 8px; margin-bottom: 7px; }
  .contacts svg { width: 20px; height: 18px; flex: none; }
  .contacts .web { font-weight: 700; font-size: 15px; margin-top: 4px; }
</style>
</head>
<body>
  <section class="card card-front">
    <div class="brand">
      <span class="brand-mark"></span>
      <span class="brand-name">Norvane Software</span>
    </div>
    <p class="slogan">Your Slogan / Tagline Here</p>
  </section>

  <section class="card card-back">
    <div class="brand">
      <span class="brand-mark"></span>
      <span class="brand-name">Norvane Software</span>
    </div>
    <div class="rules"><div class="rule"></div><div class="rule"></div></div>
    <div class="band"></div>
    <div class="holder">
      <p class="holder-name">Dana Whitlock</p>
      <p class="holder-title">FOUNDER/CEO</p>
    </div>
    <ul class="contacts">
      <li>
        <svg viewBox="0 0 20 18"><rect x="0.5" y="0.5" width="19" height="17" rx="2" fill="none" stroke="currentColor"/><path d="M5 11c0-4 10-4 10 0h-3v-2H8v2z" fill="currentColor"/></svg>
        <span>555 014 7950</span>
      </li>
      <li>
        <svg viewBox="0 0 20 18"><rect x="0.5" y="0.5" width="19" height="17" rx="2" fill="none" stroke="currentColor"/><rect x="6" y="3" width="8" height="4" fill="currentColor"/><rect x="4" y="7" width="12" height="6" fill="currentColor"/></svg>
        <span>555 014 7000</span>
      </li>
      <li>
        <svg viewBox="0 0 20 18"><rect x="0.5" y="0.5" width="19" height="17" rx="2" fill="none" stroke="currentColor"/><rect x="4" y="5" width="12" height="8" fill="none" stroke="currentColor"/><path d="M4 5l6 5 6-5" fill="none" stroke="currentColor"/></svg>
        <span>dana@norvanesoftware.com</span>
      </li>
      <li class="web">www.norvanesoftware.com</li>
    </ul>
  </section>
</body>
</html>
```